RWT Fittings Ltd Business Cards

We need a business card with our business logo. We provide window and door installations on high-rises in west coast British Colombia, Canada.

I would like my business information and details on one side of the card, and the other side the company name with logo

Target Market(s)

General Contractors

Industry/Entity Type

Construction

Contact Information for Business Card

one side i want my company name and logo in the dark theme logo that i provided

Requirements
Must have
• Marco Peltieri, 16045518293, RWTFittings@mailbox-demo.com, 1407-5194 Linden Row Burnaby BC, V5H 2K9, Owner & Manager

```html
<!DOCTYPE html>
<html lang="en">
<head>
<meta charset="utf-8">
<title>RWT Fittings Ltd Business Cards</title>
<link href="https://fonts.googleapis.com/css2?family=Open+Sans:wght@400;700&display=swap" rel="stylesheet">
<style>
  :root {
    --canvas-bg: #232323;
    --card-bg: #141414;
    --card-edge: #29abe2;
    --brand-blue: #29abe2;
    --text-light: #f2f2f2;
    --art-dark: #1b1b1b;
    --art-light: #3a3a3a;
  }
  * { box-sizing: border-box; margin: 0; padding: 0; }
  html, body {
    width: 1200px; height: 780px; overflow: hidden;
    background: var(--canvas-bg);
    font-family: "Open Sans", Arial, sans-serif;
  }
  .canvas { position: relative; width: 1200px; height: 780px; }
  .card {
    position: absolute; width: 560px; height: 320px;
    background: var(--card-bg);
    border-radius: 24px;
    border-left: 3px solid var(--card-edge);
    border-bottom: 3px solid var(--card-edge);
    overflow: hidden;
    box-shadow: 0 14px 30px rgba(0,0,0,.55);
  }
  .card--front { left: 60px; top: 50px; }
  .card--back { left: 580px; top: 410px; }

  .building-art {
    position: absolute; top: 0; bottom: 0;
    background: linear-gradient(135deg, var(--art-light) 0%, var(--art-dark) 55%, var(--card-bg) 100%);
    opacity: .85;
  }
  .card--front .building-art { left: 0; width: 230px; }
  .card--back .building-art { right: 0; width: 270px; }

  .brand-name {
    color: var(--brand-blue);
    font-weight: 700;
    letter-spacing: .5px;
    line-height: 1.1;
    white-space: nowrap;
  }
  .card--front .brand-name {
    position: absolute; right: 34px; top: 140px;
    font-size: 34px; text-align: right;
  }
  .card--back .brand-name {
    position: absolute; left: 34px; top: 32px;
    font-size: 24px;
  }

  .contact-block { position: absolute; left: 0; top: 128px; width: 270px; }
  .accent-bar {
    position: absolute; left: 0; top: 4px; width: 10px; height: 44px;
    background: var(--brand-blue);
  }
  .person-name {
    padding-left: 34px;
    color: var(--brand-blue); font-weight: 700; font-size: 20px; text-transform: uppercase;
    white-space: nowrap;
  }
  .person-role {
    padding-left: 34px; color: var(--text-light); font-size: 14px; margin-bottom: 12px;
  }
  .address {
    padding-left: 34px; color: var(--text-light); font-size: 12.5px; line-height: 1.45; margin-bottom: 12px;
  }
  .contact-list { list-style: none; padding-left: 34px; }
  .contact-list li {
    display: flex; align-items: center; gap: 8px;
    color: var(--text-light); font-size: 12.5px; line-height: 1.7; white-space: nowrap;
  }
  .contact-list svg { width: 12px; height: 12px; fill: var(--brand-blue); flex: none; }
</style>
</head>
<body>
<main class="canvas">
  <section class="card card--front" aria-label="Card front">
    <div class="building-art" role="img" aria-label="High-rise building facade with windows"></div>
    <p class="brand-name">RWT Fittings Ltd</p>
  </section>

  <section class="card card--back" aria-label="Card back">
    <div class="building-art" role="img" aria-label="High-rise building facade with windows"></div>
    <p class="brand-name">RWT Fittings Ltd</p>
    <div class="contact-block">
      <span class="accent-bar"></span>
      <h1 class="person-name">Marco Peltieri</h1>
      <p class="person-role">Owner &amp; Manager</p>
      <p class="address">1407-5194 Linden Row<br>Burnaby BC, V5H 2K9</p>
      <ul class="contact-list">
        <li><svg viewBox="0 0 24 24" aria-hidden="true"><path d="M6.6 10.8a15.1 15.1 0 0 0 6.6 6.6l2.2-2.2a1 1 0 0 1 1-.25 11.4 11.4 0 0 0 3.6.57 1 1 0 0 1 1 1V20a1 1 0 0 1-1 1A17 17 0 0 1 3 4a1 1 0 0 1 1-1h3.5a1 1 0 0 1 1 1c0 1.25.2 2.45.57 3.6a1 1 0 0 1-.25 1z"/></svg>16045518293</li>
        <li><svg viewBox="0 0 24 24" aria-hidden="true"><path d="M2 5h20v14H2z M2 5l10 8 10-8" /></svg>RWTFittings@mailbox-demo.com</li>
        <li><svg viewBox="0 0 24 24" aria-hidden="true"><circle cx="12" cy="12" r="10"/></svg>www.rwtfittings-demo.com</li>
      </ul>
    </div>
  </section>
</main>
</body>
</html>
```